Rack Card for Charter Sail Boat business in SF Bay

We are in need of a rack card design to highlight the business to tourists and locals. 2 sided card 3.86" x 8.39" (full bleed)

We are looking for visually appleaing designs on the front and back but a little more detail on the back.

Use the info provided (text and info) on the website to include the 3 key services (Quick, 1/2 day, fullday) and aspects of the boat, location and other key info for customers (not prices). DO NOT INCLUDE ALL THIS TEXT please pick the elements you would like to fit your design and inform the customer as you would like about the business.

I can also provide photos directly from the video if you think those would fit your design. If video doesn't work on this upload you can view it at the website or facebook page (www.fb.com/tidewrenmarinellc)

Target Market(s)

Tourists and locals to san francisco east bay. 25 - 55 years old. Men and women.

Industry/Entity Type

Entertainment

Colors
0455a3
ec1f27
f3f1f8

Requirements
Must have
• Highlight services, key contact information (email, phone, website site), Visual impact
• 2-sided card - 3.86" x 8.39" (98 x 213 mm)
Nice to have
• facebook link, electric engine(green),

```html
<!DOCTYPE html>
<html lang="en">
<head>
<meta charset="utf-8">
<title>Tidewren Marine – Rack Card</title>
<link rel="stylesheet" href="https://fonts.googleapis.com/css2?family=Kaushan+Script&family=Arimo:wght@400;700&family=Roboto+Condensed:wght@400;700&display=swap">
<style>
  :root{
    --navy:#0b2f6e;
    --blue:#0455a3;
    --blue-mid:#1c5fb0;
    --red:#ec1f27;
    --red-dark:#b5121a;
    --paper:#f3f1f8;
    --yellow:#ffe21a;
    --stage:#d9d9d9;
    --white:#ffffff;
  }
  *{box-sizing:border-box;margin:0;padding:0}
  html,body{width:1200px;height:1200px;overflow:hidden}
  body{background:var(--stage);font-family:"Arimo",Arial,sans-serif;position:relative}
  .card{position:absolute;top:150px;width:414px;height:900px;overflow:hidden;
        background:linear-gradient(180deg,var(--blue-mid),var(--navy));box-shadow:0 6px 18px rgba(0,0,0,.25)}
  .card--front{left:170px}
  .card--back{left:616px}
  .abs{position:absolute}
  .photo{position:absolute;border:7px solid var(--white);box-shadow:0 4px 10px rgba(0,0,0,.35)}
  .script{font-family:"Kaushan Script",cursive}
  .heading{position:absolute;font-family:"Kaushan Script",cursive;color:var(--yellow);font-size:28px;line-height:1.1;white-space:nowrap}
  .copy{position:absolute;color:var(--white);font-size:12px;line-height:1.3}

  /* front */
  .hero{left:0;top:0;width:414px;height:200px;background:linear-gradient(180deg,#6c8fb8 0%,#d8a56b 45%,#3c5c86 70%,#1d3656 100%)}
  .brand-panel{position:absolute;right:0;top:18px;width:230px;height:50px;background:rgba(255,255,255,.85);border-radius:25px 0 0 25px}
  .brand{position:absolute;right:16px;top:28px;display:flex;align-items:center;gap:8px}
  .brand__dot{width:16px;height:16px;border-radius:50%;background:var(--red)}
  .brand__name{font-family:"Kaushan Script",cursive;color:var(--blue);font-size:26px}
  .tagline{position:absolute;left:22px;top:212px;width:205px;color:var(--white);font-size:19px;line-height:1.32}
  .tagline em{font-style:normal;color:var(--yellow)}
  .booking{position:absolute;left:220px;top:690px;width:184px;padding:10px 6px;border-radius:12px;
           background:linear-gradient(180deg,var(--red),var(--red-dark));border:2px solid rgba(255,255,255,.7);
           color:var(--white);font-family:"Roboto Condensed",sans-serif;text-align:center;line-height:1.4;white-space:nowrap}
  .booking__label{font-size:12px}
  .booking__phone{font-size:16px;font-weight:700}
  .booking__mail{font-size:12.5px;font-weight:700}

  /* back */
  .trip-head{left:0;top:0;width:414px;height:140px;background:linear-gradient(180deg,#102f66,var(--blue))}
  .trip-title{position:absolute;left:18px;top:10px;color:var(--white);font-size:28px}
  .trip-copy{left:18px;top:52px;width:380px;font-size:10.5px}
  .map{left:0;top:130px;width:414px;height:640px;background:linear-gradient(160deg,#eef3f6,#cfe3ee 50%,#e7eef2)}
  .service{position:absolute;border-radius:50%;border:5px solid var(--white);box-shadow:0 4px 10px rgba(0,0,0,.35);
           color:var(--white);text-align:center;display:flex;flex-direction:column;justify-content:center;padding:0 16px}
  .service__title{font-family:"Kaushan Script",cursive;color:var(--yellow);font-size:19px;line-height:1.05;margin-bottom:6px}
  .service__text{font-size:10px;line-height:1.3}
  .service--blast{left:214px;top:120px;width:150px;height:150px;background:radial-gradient(circle at 40% 30%,#f24a50,var(--red-dark))}
  .service--half{left:28px;top:295px;width:160px;height:160px;background:radial-gradient(circle at 40% 30%,#3e68c4,#1e2f8e)}
  .service--full{left:222px;top:460px;width:160px;height:160px;background:radial-gradient(circle at 40% 30%,#36a852,#0f6426)}
  .contact-title{position:absolute;left:150px;top:772px;color:var(--white);font-size:34px}
  .badge{position:absolute;left:20px;top:778px;width:58px;height:58px;border-radius:50%;background:var(--paper);border:4px solid var(--yellow)}
  .contact-line{position:absolute;display:flex;align-items:center;gap:6px;color:var(--white);
                font-family:"Roboto Condensed",sans-serif;font-weight:700;font-size:12.5px;white-space:nowrap}
  .contact-line svg{width:15px;height:15px;flex:none}
</style>
</head>
<body>

<section class="card card--front">
  <div class="abs hero" role="img" aria-label="Photo of the sailboat deck and rigging at sunset over the bay"></div>
  <div class="brand-panel"></div>
  <div class="brand"><span class="brand__dot"></span><span class="brand__name">Tidewren Marine</span></div>

  <svg class="abs" style="left:0;top:150px" width="414" height="110" viewBox="0 0 414 110">
    <path d="M0 60 C120 20 260 20 414 40 L414 110 L0 110 Z" fill="#1c5fb0"/>
    <path d="M0 52 C130 10 270 10 414 28 L414 40 C260 22 120 24 0 66 Z" fill="#ec1f27"/>
    <path d="M0 70 C130 28 270 28 414 50 L414 62 C270 42 130 44 0 84 Z" fill="#ffffff"/>
  </svg>

  <div class="photo" role="img" aria-label="Photo of sparkling bay water and distant hills"
       style="left:210px;top:105px;width:160px;height:115px;transform:rotate(7deg);background:linear-gradient(180deg,#7aa6d8,#2a5f9c 55%,#1b3f70)"></div>
  <div class="photo" role="img" aria-label="Photo of the sailboat moored at the marina"
       style="left:252px;top:232px;width:145px;height:110px;transform:rotate(-4deg);background:linear-gradient(180deg,#8db7e4,#5d86b0 50%,#22415f)"></div>
  <div class="photo" role="img" aria-label="Photo of the sails and deck under way"
       style="left:30px;top:385px;width:165px;height:115px;transform:rotate(5deg);background:linear-gradient(180deg,#6b9ad8,#c9d6e6 50%,#2f4f7a)"></div>
  <div class="photo" role="img" aria-label="Photo of the boat's cabin interior"
       style="left:88px;top:510px;width:135px;height:100px;transform:rotate(4deg);background:linear-gradient(180deg,#c29468,#7d5236 60%,#3e2a1f)"></div>

  <p class="tagline script">Enjoy an amazing experience aboard <em>Tidewren</em> and view San Francisco and the rest of the bay</p>

  <h2 class="heading" style="left:238px;top:360px">Modern</h2>
  <p class="copy" style="left:238px;top:400px;width:165px">Tidewren is completely electric which means no diesel smells, noise or vibration to suffer. New electrics, plumbing, toilets, and deck areas compliment the elegant lines.</p>

  <h2 class="heading" style="left:238px;top:518px">Entertaining</h2>
  <p class="copy" style="left:238px;top:558px;width:168px;font-size:11.5px">Experience the thrill of sailing Tidewren while we explore Alcatraz and Angel Islands, the Golden Gate and Bay Bridges, the City front or the many other hidden gems.</p>

  <h2 class="heading" style="left:22px;top:640px">Safe</h2>
  <p class="copy" style="left:22px;top:684px;width:190px;font-size:12.5px">We carry aboard everything to make your time aboard safe. Life preservers and USCG bulky ones as well as modern self inflating slim comfortable life jackets. Also loaded for every trip is a complete first aid kit, AED, EPIRB, and many other safety items.</p>

  <div class="booking">
    <div class="booking__label">For Bookings Contact us Today</div>
    <div class="booking__phone">+1 (555) 014 SAIL (7245)</div>
    <div class="booking__mail">Bookings@TidewrenMarine.com</div>
  </div>
</section>

<section class="card card--back">
  <div class="abs map" role="img" aria-label="Map of San Francisco Bay with the three charter routes"></div>
  <div class="abs trip-head"></div>
  <svg class="abs" style="left:0;top:115px" width="414" height="60" viewBox="0 0 414 60">
    <path d="M0 0 L414 0 L414 30 C280 55 140 40 0 20 Z" fill="#0455a3"/>
    <path d="M0 20 C140 40 280 55 414 30 L414 36 C280 62 140 46 0 26 Z" fill="#ec1f27"/>
    <path d="M0 26 C140 46 280 62 414 36 L414 42 C280 68 140 52 0 32 Z" fill="#ffffff"/>
  </svg>
  <h2 class="trip-title script">The trip</h2>
  <p class="copy trip-copy">When chartering Tidewren, the vessel is yours to direct anywhere within the time you wish to enjoy her. We do have a few old favorites that are always fun that we have listed below. These are just to provide an idea of the possible cruise as every trip takes into account your ideas and natures (tides, weather and currents) will. Our custom trips are simple to arrange and book, we simply ask for a minimum of 3 hours duration.</p>

  <svg class="abs" style="left:0;top:130px" width="414" height="640" viewBox="0 0 414 640">
    <path d="M0 150 C120 190 250 150 414 170" stroke="#1c4fa0" stroke-width="3" fill="none"/>
    <path d="M0 330 C130 300 260 340 414 320" stroke="#1c4fa0" stroke-width="3" fill="none"/>
  </svg>

  <div class="service service--blast">
    <div class="service__title">2 hours Blast</div>
    <div class="service__text">Could be a sunset sail, an early morning wake up cruise or a blast out into the bay anytime to find peace, fresh air and amazing views.</div>
  </div>
  <div class="service service--half">
    <div class="service__title">1/2 day Fun</div>
    <div class="service__text">A full morning, afternoon or evening out in the Bay seeing many of the main features and landmarks close to the Bay from the water. Actual duration 4.5 hours</div>
  </div>
  <div class="service service--full">
    <div class="service__title">Full Day Adventure</div>
    <div class="service__text">The day includes a complete circuit of the Bay and lunch at anchor. Actual duration 7-8 hours</div>
  </div>

  <svg class="abs" style="left:0;top:700px" width="414" height="200" viewBox="0 0 414 200">
    <path d="M0 50 C140 80 280 60 414 10 L414 200 L0 200 Z" fill="#ec1f27"/>
    <path d="M0 58 C140 88 280 68 414 18 L414 200 L0 200 Z" fill="#ffffff"/>
    <path d="M0 64 C140 94 280 74 414 24 L414 200 L0 200 Z" fill="#123b7a"/>
  </svg>

  <div class="badge"></div>
  <h2 class="contact-title script">Contact</h2>

  <div class="contact-line" style="left:100px;top:828px">
    <svg viewBox="0 0 16 16"><path d="M4 1 L6.5 4 L5 6 C6 8.5 7.5 10 10 11 L12 9.5 L15 12 L13 15 C7 14.5 1.5 9 1 3 Z" fill="#fff"/></svg>
    +1 (555) 014 SAIL (7245)
  </div>
  <div class="contact-line" style="left:100px;top:850px">
    <svg viewBox="0 0 16 16"><rect x="1" y="3" width="14" height="10" fill="none" stroke="#fff" stroke-width="1.4"/><path d="M1 3 L8 9 L15 3" fill="none" stroke="#fff" stroke-width="1.4"/></svg>
    Bookings@TidewrenMarine.com
  </div>
  <div class="contact-line" style="left:100px;top:872px">
    <svg viewBox="0 0 16 16"><circle cx="8" cy="8" r="6.5" fill="none" stroke="#fff" stroke-width="1.3"/><ellipse cx="8" cy="8" rx="3" ry="6.5" fill="none" stroke="#fff" stroke-width="1.1"/><path d="M1.5 8 H14.5" stroke="#fff" stroke-width="1.1"/></svg>
    www.tidewrenmarine.com
  </div>
  <div class="contact-line" style="left:272px;top:872px">
    <svg viewBox="0 0 16 16"><circle cx="8" cy="8" r="7" fill="none" stroke="#fff" stroke-width="1.4"/></svg>
    /tidewrenmarinellc
  </div>
</section>

</body>
</html>
```